Equipment Finance Specialist I work with companies who need the funds to buy their equipment

I would like a business card that stands out on the shelves. I want to be able to hand it to someone and say WOW. This card should have my logo.
You can put color into it I am very open on design and color

What my company does is we deal with dealerships that sell equipment such as Dump Trucks garbage trucks tractors trailers. Customers get referred to us and depending on their time in business we will ask for the following items

Companies that have been in business for more than two years we have a credit application program up to 250K . With this program we need the following items Credit application filled out(which is what I would like to be able for the customer to click on my website to get.) as well as three current month bank statements.

Deals over 250k we will need the following items

2 years business tax returns
2 years personal tax returns
Profit & Loss statement
Personal Financial Statement

what we do
100% FINANCING
SEASONAL PAYMENTS
LOAN BALLOON PAYMENTS
TRAC LEASING
LOW-INTEREST REFINANCING RATES
DEBT CONSOLIDATION

We specialize in creative financing solutions and offer a variety of reliable, flexible and expandable lending choices.

Target Market(s)

Trucking Companies

Industry/Entity Type

Trucking Company

Contact Information for Business Card

* $250,000 Application only Program
* Loans from $30,000 to 5,000,000
* Competitive Interest Rates

Font styles to use
Serif
Sans Serif

Colors

Designer to choose colors to be used in the design.

Requirements
Must have
• On the back of the card.
• * $250,000 Application only Program
• * Loans from $30,000 to 5,000,000
• My name, email, website. address
• * Competitive Interest Rates
• * 100% Financing
Nice to have
• I want my logo to pop on the card
• My logo is the great one I would like to use
Should not have
• I am up for your creativity as well

```html
<!DOCTYPE html>
<html lang="en">
<head>
<meta charset="utf-8">
<title>Keystone Funding – Business Card</title>
<link rel="stylesheet" href="https://fonts.googleapis.com/css2?family=Open+Sans:wght@400;700&display=swap">
<style>
  :root {
    --navy: #012868;
    --red: #bd0b2e;
    --white: #ffffff;
    --backdrop: #e6e6e6;
  }
  * { margin: 0; padding: 0; box-sizing: border-box; }
  html, body {
    width: 1125px;
    height: 1200px;
    overflow: hidden;
    background: var(--backdrop);
    font-family: "Open Sans", sans-serif;
  }
  .card {
    position: absolute;
    left: 150px;
    width: 826px;
    height: 471px;
    overflow: hidden;
  }
  .card--front { top: 98px; background: var(--navy); }
  .card--back { top: 631px; background: var(--red); }

  .front-shape { position: absolute; inset: 0; }

  .contact {
    position: absolute;
    left: 38px;
    top: 118px;
    color: var(--white);
  }
  .contact__name {
    font-size: 28px;
    font-weight: 700;
    line-height: 1.1;
    letter-spacing: 0.3px;
  }
  .contact__title {
    font-size: 20px;
    font-weight: 400;
    margin-top: 2px;
  }
  .contact__address {
    font-size: 19px;
    line-height: 26px;
    margin-top: 20px;
  }
  .contact__list {
    list-style: none;
    margin-top: 14px;
    font-size: 19px;
    line-height: 27px;
  }
  .contact__list li {
    display: flex;
    align-items: center;
  }
  .contact__icon {
    width: 18px;
    height: 18px;
    margin-right: 16px;
    flex: none;
  }

  .brand {
    position: absolute;
    left: 398px;
    top: 210px;
    width: 390px;
    display: flex;
    align-items: center;
    justify-content: center;
    gap: 14px;
  }
  .brand__dot {
    width: 26px;
    height: 26px;
    border-radius: 50%;
    background: var(--navy);
    flex: none;
  }
  .brand__name {
    font-size: 36px;
    font-weight: 700;
    color: var(--navy);
    letter-spacing: 0.5px;
    white-space: nowrap;
  }

  .back-brand {
    position: absolute;
    left: 0;
    right: 0;
    top: 190px;
    display: flex;
    align-items: center;
    justify-content: center;
    gap: 14px;
  }
  .back-brand__dot {
    width: 26px;
    height: 26px;
    border-radius: 50%;
    background: var(--white);
  }
  .back-brand__name {
    font-size: 36px;
    font-weight: 700;
    color: var(--white);
    letter-spacing: 0.5px;
  }

  .offers {
    position: absolute;
    left: 0;
    right: 0;
    top: 380px;
    text-align: center;
    color: var(--white);
    font-size: 20px;
    line-height: 26px;
  }
</style>
</head>
<body>

<section class="card card--front">
  <svg class="front-shape" viewBox="0 0 826 471" width="826" height="471" aria-hidden="true">
    <ellipse cx="795" cy="235" rx="472" ry="272" fill="var(--red)"/>
    <ellipse cx="803" cy="235" rx="466" ry="269" fill="var(--white)"/>
  </svg>

  <div class="contact">
    <div class="contact__name">MARCUS HALE</div>
    <div class="contact__title">PRESIDENT</div>
    <div class="contact__address">4217 Linden Park Road<br>Maple Grove, NY 11020</div>
    <ul class="contact__list">
      <li>
        <svg class="contact__icon" viewBox="0 0 18 18" aria-hidden="true">
          <path d="M2 6c0-3 3-4 7-4s7 1 7 4v1h-4V5H6v2H2z" fill="var(--white)"/>
          <rect x="3" y="9" width="12" height="7" rx="1.5" fill="var(--white)"/>
          <circle cx="9" cy="12.5" r="2" fill="var(--navy)"/>
        </svg>
        <span>555 0142 7736</span>
      </li>
      <li>
        <svg class="contact__icon" viewBox="0 0 18 18" aria-hidden="true">
          <rect x="1.5" y="4.5" width="15" height="10" fill="var(--white)"/>
          <path d="M1.5 4.5 9 10l7.5-5.5" fill="none" stroke="var(--navy)" stroke-width="1.4"/>
        </svg>
        <span>marcus@keystonefunding.com</span>
      </li>
      <li>
        <svg class="contact__icon" viewBox="0 0 18 18" aria-hidden="true">
          <circle cx="9" cy="9" r="7.5" fill="var(--white)"/>
          <path d="M5 6c2 0 3 1 3 3s-2 2-2 4M11 4c0 2 2 2 3 3M10 14c1-2 3-2 4-3" fill="none" stroke="var(--navy)" stroke-width="1.6"/>
        </svg>
        <span>www.keystonefunding.com</span>
      </li>
    </ul>
  </div>

  <div class="brand">
    <span class="brand__dot"></span>
    <span class="brand__name">KEYSTONE FUNDING</span>
  </div>
</section>

<section class="card card--back">
  <div class="back-brand">
    <span class="back-brand__dot"></span>
    <span class="back-brand__name">KEYSTONE FUNDING</span>
  </div>
  <p class="offers">
    $250,000 Application only Program &#9679; Loans from $30,000 to 5,000,000<br>
    Competitive Interest Rates &#9679; 100% Financing
  </p>
</section>

</body>
</html>
```